Flat bootstrap design for existing site

I'm looking for a modern flat design based around an existing logo. This has to be a custom design (no external templates), and implemented into a bootstrap framework.

The logo is attached as 2 versions - choose whichever you want, that flows better with whatever design you choose.

Added screenshots of the existing site (currently using the default bootstrap layouts). Please make your designs around those pages in the screenshots (i.e. the homepage only has the postal code input and the header). The active page has 3 screenshots, because I wanted to illustrate the other states that would be visible (in the table rows).

This is a moving/junk removal website, just for some context.

Here's some example websites (flat designs) that I like, just to give you an idea of what I'm after.

https://www.plimvora.com/
https://dacklow.com/
https://trevanu.com/
https://quobrintal.com/en/

Coding

Coded - Design and coding required

Number of Pages Required

5+ page

Colors

Designer to choose colors to be used in the design.

Requirements
Must have
• It must be a modern/simple flat design, that is built around the existing logo (attached).
• It has to be implemented using bootstrap.

```html
<!DOCTYPE html>
<html lang="en">
<head>
<meta charset="utf-8">
<title>Haulvane – Booking details</title>
<link href="https://fonts.googleapis.com/css2?family=Raleway:wght@400;500;600&display=swap" rel="stylesheet">
<style>
:root{
  --brand:#55cdf5;
  --brand-deep:#47c6f2;
  --ink:#333;
  --text:#666;
  --muted:#888;
  --panel:#f8f8f8;
  --line:#e6e6e6;
  --white:#fff;
  --badge:#7d7b80;
}
*{box-sizing:border-box;margin:0;padding:0}
html,body{width:1200px;height:1009px;overflow:hidden}
body{font-family:'Raleway',sans-serif;color:var(--text);background:var(--white);position:relative}
.site-header{position:absolute;top:0;left:0;width:1200px;height:75px;background:linear-gradient(90deg,var(--brand),var(--brand-deep))}
.brand{position:absolute;left:99px;top:20px;display:flex;align-items:center;gap:8px;color:var(--white);font-weight:600;font-size:28px;letter-spacing:1px}
.brand-dot{width:14px;height:14px;border-radius:50%;background:var(--white)}
.main-nav{position:absolute;top:0;left:560px;height:75px;display:flex}
.main-nav a{color:var(--white);text-decoration:none;font-size:13.5px;font-weight:500;line-height:75px;padding:0 22px;display:block}
.main-nav a.active{background:var(--white);color:var(--brand);width:158px;text-align:center;padding:0}
.main-nav a.account{padding-left:23px}
.caret{display:inline-block;border:4px solid transparent;border-top:5px solid var(--white);margin-left:6px;vertical-align:-1px}

.booking-panel{position:absolute;left:99px;top:99px;width:1003px;height:384px;background:var(--panel);border:1px solid var(--line)}
.panel-title{position:absolute;left:27px;top:27px;font-size:15.5px;font-weight:500;color:var(--ink)}
.panel-rule{position:absolute;left:27px;top:61px;width:939px;border-top:1px solid var(--line)}
.field-label{position:absolute;font-size:15px;color:var(--text)}
.field{position:absolute;height:46px;background:var(--white);border:1px solid var(--line);border-radius:2px;font-size:12.5px;color:var(--text);padding:0 20px;display:flex;align-items:center;justify-content:space-between}
.btn-update{position:absolute;left:28px;top:306px;width:120px;height:46px;background:var(--brand);color:var(--white);border:0;border-radius:2px;font-family:inherit;font-weight:600;font-size:13px;letter-spacing:1.5px}

.section-rule{position:absolute;left:99px;top:514px;width:1003px;border-top:1px solid var(--line)}
.section-title{position:absolute;left:98px;top:539px;font-size:15.5px;font-weight:500;color:var(--ink)}
.notice{position:absolute;left:99px;top:577px;width:1003px;height:46px;background:var(--panel);border:1px solid var(--line);border-radius:2px;font-size:12.5px;color:var(--text);padding-left:20px;line-height:44px}

.drivers-table{position:absolute;left:99px;top:640px;width:1003px;border-collapse:collapse}
.drivers-table th{text-align:left;font-size:14.5px;font-weight:500;color:var(--ink);height:48px;border-bottom:1px solid var(--line)}
.drivers-table td{font-size:12.5px;color:var(--text);height:62px;border-bottom:1px solid var(--line)}
.col-name{width:167px}.col-dist{width:193px}.col-time{width:285px}
.badge{display:inline-block;width:103px;height:26px;line-height:26px;text-align:center;background:var(--badge);color:var(--white);border-radius:2px;font-size:12px}

.site-footer{position:absolute;left:0;top:962px;width:1200px;height:47px;background:linear-gradient(90deg,var(--brand),var(--brand-deep));color:var(--white);font-size:12.5px;text-align:center;line-height:47px}
</style>
</head>
<body>
<header class="site-header">
  <div class="brand"><span class="brand-dot"></span>HAULVANE</div>
  <nav class="main-nav">
    <a href="#">BOOK</a>
    <a href="#">HOW IT WORKS</a>
    <a href="#" class="active">BECOME A DRIVER</a>
    <a href="#" class="account">maren@qvtelpa.com<span class="caret"></span></a>
  </nav>
</header>

<section class="booking-panel">
  <h2 class="panel-title">BOOKING DETAILS</h2>
  <div class="panel-rule"></div>
  <label class="field-label" style="left:27px;top:88px">Package Selected :</label>
  <label class="field-label" style="left:504px;top:88px">Pick-up time selected :</label>
  <div class="field" style="left:28px;top:130px;width:469px">Package 1
    <svg width="9" height="13" viewBox="0 0 9 13"><path d="M4.5 0L9 5H0zM4.5 13L0 8h9z" fill="#555"/></svg>
  </div>
  <div class="field" style="left:505px;top:130px;width:470px">July 18 at 4:13am
    <svg width="13" height="14" viewBox="0 0 13 14" fill="none" stroke="#666" stroke-width="1.2"><rect x="0.6" y="2" width="11.8" height="11.4"/><path d="M0.6 5h11.8M3.5 0v3M9.5 0v3M3 7.5h7M3 10.5h7M5 5v8M8 5v8"/></svg>
  </div>
  <label class="field-label" style="left:27px;top:198px">Description</label>
  <div class="field" style="left:28px;top:240px;width:944px">1 large stove</div>
  <button class="btn-update">UPDATE</button>
</section>

<div class="section-rule"></div>
<h2 class="section-title">DRIVERS IN YOUR AREA</h2>
<div class="notice">Please Stay on this page and be patient,While we contact the drivers and find you one ASAP.</div>

<table class="drivers-table">
  <thead><tr><th class="col-name">Name</th><th class="col-dist">Distance (km)</th><th class="col-time">Agreed Pick-up time</th><th></th></tr></thead>
  <tbody>
    <tr><td>Darin Holloway</td><td>4.04km away</td><td>-</td><td><span class="badge">Pending</span></td></tr>
    <tr><td>Pieter Lund</td><td>5.7km away</td><td>-</td><td><span class="badge">Pending</span></td></tr>
    <tr><td>Osric Vale</td><td>11.13km away</td><td>-</td><td><span class="badge">Pending</span></td></tr>
    <tr><td>Corwin Abbey</td><td>11.91km away</td><td>-</td><td><span class="badge">Pending</span></td></tr>
  </tbody>
</table>

<footer class="site-footer">© copyright 2017 Haulvane.All Rights Reserved</footer>
</body>
</html>
```